Ledgerwise Forge - WordPress Theme & Logo

Design a logo and Wordpress website design for Ledgerwise Forge. Ledgerwise Forge provides cryptocurrency development services to clients who need a team to create & continue developing a new cryptocurrency or who want to replace their current cryptocurrency development team. more details in the attached document.
Updates

Target Market(s)

Entrepreneurs who are building a business / platform that makes use of an underlying cryptocurrency.

Logo Text

LF or Ledgerwise Forge

Coding

Coded - Design and coding required

Font styles to use
Sans Serif

Requirements
Must have
• Professional logo, complete coded Wordpress theme for all pages, containing all specified links and buttons
Nice to have
• It would be nice if the buttons that are meant to integrate with Dealtrail contain the necessary code for that. I can provide any necessary Dealtrail details from my account.
Should not have
• Slow loading time

```html
<!DOCTYPE html>
<html lang="en">
<head>
<meta charset="utf-8">
<title>Ledgerwise Forge</title>
<link href="https://fonts.googleapis.com/css2?family=Montserrat:wght@600;700&family=Roboto:wght@400;500;700&display=swap" rel="stylesheet">
<style>
:root{
  --blue:#1f4fa6;
  --blue-bright:#2a62c4;
  --navy:#152a6e;
  --navy-deep:#0d1a45;
  --ink:#2b2b2b;
  --body:#555;
  --muted:#777;
  --panel:#f4f4f5;
  --white:#fff;
  --star:#f3c316;
}
*{box-sizing:border-box;margin:0;padding:0}
html,body{width:1200px;height:3951px;overflow:hidden;background:var(--white)}
body{position:relative;font-family:"Roboto",sans-serif;color:var(--body)}
.abs{position:absolute}
h1,h2,h3{font-family:"Montserrat",sans-serif;color:var(--ink)}
.section-title{position:absolute;left:0;width:1200px;text-align:center;font-size:27px;font-weight:700;text-transform:uppercase}
.section-title::after{content:"";display:block;width:156px;height:4px;background:var(--blue);margin:12px auto 0}

/* header */
.site-header{position:absolute;top:0;left:0;width:1200px;height:81px;background:var(--white);border-top:4px solid var(--blue)}
.brand{position:absolute;display:flex;align-items:center;gap:10px}
.brand-mark{width:40px;height:40px;border-radius:50%;background:var(--blue)}
.brand-name{font-family:"Montserrat",sans-serif;font-weight:700;color:var(--navy);line-height:1.05;text-transform:uppercase}
.site-header .brand{left:110px;top:14px}
.site-header .brand-name{font-size:15px}
.main-nav{position:absolute;left:324px;top:30px;display:flex;gap:23px;font-size:15px;color:var(--ink)}
.main-nav .current{color:var(--blue)}
.btn{display:inline-block;border-radius:30px;font-family:"Roboto",sans-serif;font-weight:700;text-transform:uppercase;text-align:center;color:var(--white);background:linear-gradient(90deg,var(--navy),var(--blue-bright))}
.header-cta{position:absolute;left:861px;top:16px;width:228px;height:48px;line-height:48px;font-size:14px;box-shadow:0 3px 8px rgba(20,40,110,.3)}

/* hero */
.hero{position:absolute;top:81px;left:0;width:1200px;height:680px;background:radial-gradient(circle at 70% 35%,#3a4a6c 0%,#1a2847 35%,#0b1530 75%)}
.hero-text{position:absolute;left:110px;top:195px;font-family:"Montserrat",sans-serif;font-weight:700;font-size:25px;line-height:36px;color:var(--white);text-transform:uppercase}
.hero-btn{position:absolute;left:110px;top:330px;width:198px;height:48px;line-height:48px;font-size:14px}
.hero-curve{position:absolute;top:560px;left:0}

/* welcome */
.welcome{position:absolute;top:760px;left:0;width:1200px;height:257px;background:var(--panel)}
.welcome p{position:absolute;left:200px;top:135px;width:800px;text-align:center;font-size:15px;line-height:26px;color:var(--muted)}

/* why */
.feature{position:absolute;top:1197px;width:316px;height:307px;text-align:center}
.feature.raised{background:var(--white);border-radius:18px;box-shadow:0 4px 14px rgba(0,0,0,.13);overflow:hidden}
.feature.raised::after{content:"";position:absolute;left:36px;right:36px;bottom:0;height:5px;background:var(--blue);border-radius:3px 3px 0 0}
.feature-icon{width:102px;height:102px;border-radius:50%;background:#333;margin:38px auto 0;display:flex;align-items:center;justify-content:center}
.feature.raised .feature-icon{background:var(--blue)}
.feature h3{font-size:20px;margin-top:26px;font-weight:600}
.feature h3::after{content:"";display:block;width:48px;height:3px;background:var(--blue);margin:8px auto 0}
.feature p{font-size:15.5px;line-height:25px;color:var(--ink);margin:16px 28px 0}

/* services */
.services{position:absolute;top:1596px;left:0;width:1200px;height:583px;background:radial-gradient(circle at 20% 30%,#2b4aa0 0%,#17307d 40%,#122470 100%)}
.services .section-title{color:var(--white);top:50px}
.service{position:absolute;top:138px;width:317px;height:391px;background:var(--white);border-radius:8px;padding:6px}
.service-img{height:195px;border-radius:6px}
.service h3{font-family:"Roboto",sans-serif;color:var(--blue);font-size:18px;font-weight:500;margin:15px 8px 10px}
.service ul{list-style:none;margin:0 8px}
.service li{position:relative;padding-left:28px;font-size:13.5px;line-height:21px;color:var(--ink);margin-bottom:3px}
.service li svg{position:absolute;left:0;top:4px}
.learn{position:absolute;left:14px;bottom:18px;font-size:14px;font-weight:700;color:var(--blue);display:flex;align-items:center;gap:10px}

/* about */
.about-ring{position:absolute;left:110px;top:2272px;width:456px;height:456px;border-radius:50%;background:var(--navy)}
.about-img{position:absolute;left:128px;top:2274px;width:438px;height:438px;border-radius:50%;border:6px solid var(--white);background:linear-gradient(120deg,#6b5240 0%,#2f3442 50%,#1d2e55 100%);box-shadow:0 3px 10px rgba(0,0,0,.2)}
.about-title{position:absolute;left:613px;top:2322px;font-size:35px;font-weight:700;text-transform:uppercase;display:flex;align-items:center;gap:24px}
.about-title::after{content:"";width:94px;height:4px;background:var(--blue)}
.about-copy{position:absolute;left:613px;top:2380px;width:477px;font-size:14px;line-height:24px;color:var(--muted);text-align:justify}
.about-copy p+p{margin-top:14px}
.about-btn{position:absolute;left:613px;top:2615px;width:145px;height:49px;line-height:49px;font-size:15px}

/* testimonials */
.review{position:absolute;top:2919px;width:318px;height:221px;background:var(--white);border-top:4px solid var(--blue);border-radius:20px 20px 8px 8px;box-shadow:0 2px 8px rgba(0,0,0,.12);text-align:center}
.avatar{position:absolute;left:50%;top:-36px;margin-left:-38px;width:76px;height:76px;border-radius:50%;border:4px solid var(--blue);background:linear-gradient(160deg,#c9ced6,#5c6472)}
.review h3{font-family:"Roboto",sans-serif;font-size:19px;font-weight:500;margin-top:52px}
.stars{color:var(--star);font-size:11px;letter-spacing:2px;margin-top:3px}
.review p{font-size:14px;line-height:25px;color:var(--muted);margin:12px 12px 0}

/* cta */
.cta{position:absolute;top:3235px;left:0;width:1200px;height:466px;background:linear-gradient(160deg,#1b2f86 0%,#2a55b4 55%,#3d78d4 100%)}
.cta h2{position:absolute;left:0;width:1200px;top:57px;text-align:center;color:var(--white);font-size:27px;text-transform:uppercase}
.cta p{position:absolute;left:160px;width:880px;top:122px;text-align:center;color:var(--white);font-size:14px;line-height:25px}
.cta-btn{position:absolute;left:529px;top:219px;width:143px;height:49px;line-height:49px;font-size:14px;background:var(--white);color:var(--blue)}
.cta-curve{position:absolute;top:3540px;left:0}

/* footer */
.site-footer{position:absolute;top:3700px;left:0;width:1200px;height:251px;background:var(--panel)}
.site-footer .brand{left:110px;top:12px}
.site-footer .brand-mark{width:56px;height:56px}
.site-footer .brand-name{font-size:20px;font-weight:600}
.socials{position:absolute;left:142px;top:119px;display:flex;gap:5px}
.socials span{width:35px;height:35px;border-radius:50%;border:2px solid var(--navy)}
.socials span:first-child{background:var(--navy)}
.foot-col{position:absolute;top:12px}
.foot-col h4{font-size:17px;font-weight:500;color:var(--navy)}
.foot-col h4::after{content:"";display:block;width:46px;height:2px;background:var(--blue);margin-top:5px}
.foot-col ul{list-style:none;margin-top:14px}
.foot-col li{font-size:14.5px;line-height:25px;color:var(--ink);display:flex;align-items:center;gap:16px}
.newsletter{position:absolute;left:780px;top:52px;width:308px;height:50px;border-radius:25px;background:var(--white);border:1px solid #ddd;font-size:14px;color:var(--muted);padding:15px 16px}
.newsletter b{position:absolute;right:5px;top:5px;width:38px;height:38px;border-radius:50%;background:var(--blue);display:flex;align-items:center;justify-content:center}
.foot-rule{position:absolute;left:125px;top:198px;width:950px;height:1px;background:#ddd}
.copyright{position:absolute;left:0;width:1200px;top:214px;text-align:center;font-size:12px;color:var(--ink)}
</style>
</head>
<body>

<header class="site-header">
  <div class="brand"><span class="brand-mark"></span><span class="brand-name">Ledgerwise<br>Forge</span></div>
  <nav class="main-nav"><span class="current">Home</span><span>About Us</span><span>Services</span><span>Our Methods</span><span>Testimonials</span><span>Blog</span></nav>
  <a class="btn header-cta">Schedule Consultation</a>
</header>

<section class="hero">
  <div class="abs" role="img" aria-label="Glowing wireframe cube over a blue blockchain network background" style="inset:0"></div>
  <h1 class="hero-text">Your own cryptocurrency.<br>Secure, easy to use, and<br>built by an expert team.</h1>
  <a class="btn hero-btn">Download Free PDF</a>
</section>
<svg class="hero-curve" width="1200" height="210" viewBox="0 0 1200 210">
  <path d="M0,53 Q600,358 1200,30 L1200,210 L0,210 Z" fill="#f4f4f5"/>
  <path d="M0,53 Q600,358 1200,30" fill="none" stroke="#1f4fa6" stroke-width="5"/>
</svg>

<section class="welcome">
  <h2 class="section-title" style="top:55px">Welcome to Ledgerwise Forge</h2>
  <p>Ledgerwise Forge adds professionalism to cryptocurrency development. Our done-for-you service covers everything from development and IT operations to ongoing support. You have access to a full team, for less than the typical cost of a single developer.</p>
</section>

<h2 class="section-title" style="top:1106px">Why Choose Us</h2>
<div class="feature" style="left:110px">
  <div class="feature-icon"><svg width="54" height="54" viewBox="0 0 54 54" fill="none" stroke="#fff" stroke-width="2"><path d="M18 10h18l5 6-14 14-14-14z M13 16h28 M6 36h10l8 4h10a3 3 0 0 1 0 6H22 M34 42l12-6a3 3 0 0 1 3 5L36 49H6"/></svg></div>
  <h3>VALUE</h3>
  <p>A team of experts, regular updates, and fixed costs</p>
</div>
<div class="feature raised" style="left:442px">
  <div class="feature-icon"><svg width="54" height="54" viewBox="0 0 54 54" fill="none" stroke="#fff" stroke-width="2"><circle cx="24" cy="20" r="8"/><path d="M13 20a11 11 0 0 1 22 0 M10 46c0-8 6-13 14-13s14 5 14 13z"/><circle cx="42" cy="38" r="5"/></svg></div>
  <h3>SUPPORT</h3>
  <p>Receive advice and other services, beyond development.</p>
</div>
<div class="feature" style="left:773px">
  <div class="feature-icon"><svg width="54" height="54" viewBox="0 0 54 54" fill="none" stroke="#fff" stroke-width="2"><rect x="13" y="8" width="28" height="38"/><path d="M19 15h16 M19 20h16"/><circle cx="27" cy="31" r="5"/><path d="M24 35l-2 7 5-2 5 2-2-7"/></svg></div>
  <h3>COMMITMENT</h3>
  <p>Enjoy regular updates and new features.</p>
</div>

<section class="services">
  <div class="abs" role="img" aria-label="Faint blue digital network backdrop" style="inset:0"></div>
  <h2 class="section-title">Our Services</h2>
  <article class="service" style="left:110px">
    <div class="service-img" role="img" aria-label="Laptop with world map and currency icons" style="background:linear-gradient(135deg,#d9dde3,#4a5a78 60%,#1d2a44)"></div>
    <h3>Ledgerwise Creation &amp; Launch</h3>
    <ul><li><svg width="13" height="13" viewBox="0 0 13 13"><circle cx="6.5" cy="6.5" r="5.5" fill="none" stroke="#1f4fa6" stroke-width="1.5"/><path d="M4 6.5l2 2 3-4" fill="none" stroke="#1f4fa6" stroke-width="1.5"/></svg>Base fixed price for cryptocurrency development &amp; launch–would be customizable based on client requirements</li></ul>
    <span class="learn">Learn More <svg width="14" height="14" viewBox="0 0 14 14"><circle cx="7" cy="7" r="6" fill="none" stroke="#1f4fa6" stroke-width="1.6"/><path d="M4 7h6M7.5 4.5L10 7 7.5 9.5" fill="none" stroke="#1f4fa6" stroke-width="1.6"/></svg></span>
  </article>
  <article class="service" style="left:442px">
    <div class="service-img" role="img" aria-label="Hands holding a glowing coin in a digital network" style="background:linear-gradient(135deg,#9aa6bb,#3c4e72 55%,#1b2744)"></div>
    <h3>Basic Offering</h3>
    <ul>
      <li><svg width="13" height="13" viewBox="0 0 13 13"><circle cx="6.5" cy="6.5" r="5.5" fill="none" stroke="#1f4fa6" stroke-width="1.5"/><path d="M4 6.5l2 2 3-4" fill="none" stroke="#1f4fa6" stroke-width="1.5"/></svg>Lower cost per month</li>
      <li><svg width="13" height="13" viewBox="0 0 13 13"><circle cx="6.5" cy="6.5" r="5.5" fill="none" stroke="#1f4fa6" stroke-width="1.5"/><path d="M4 6.5l2 2 3-4" fill="none" stroke="#1f4fa6" stroke-width="1.5"/></svg>Slower release schedule</li>
      <li><svg width="13" height="13" viewBox="0 0 13 13"><circle cx="6.5" cy="6.5" r="5.5" fill="none" stroke="#1f4fa6" stroke-width="1.5"/><path d="M4 6.5l2 2 3-4" fill="none" stroke="#1f4fa6" stroke-width="1.5"/></svg>Client assists with testing new releases</li>
      <li><svg width="13" height="13" viewBox="0 0 13 13"><circle cx="6.5" cy="6.5" r="5.5" fill="none" stroke="#1f4fa6" stroke-width="1.5"/><path d="M4 6.5l2 2 3-4" fill="none" stroke="#1f4fa6" stroke-width="1.5"/></svg>Less input into future roadmap/features</li>
    </ul>
    <span class="learn">Learn More <svg width="14" height="14" viewBox="0 0 14 14"><circle cx="7" cy="7" r="6" fill="none" stroke="#1f4fa6" stroke-width="1.6"/><path d="M4 7h6M7.5 4.5L10 7 7.5 9.5" fill="none" stroke="#1f4fa6" stroke-width="1.6"/></svg></span>
  </article>
  <article class="service" style="left:772px">
    <div class="service-img" role="img" aria-label="Hand holding a phone showing a trading chart" style="background:linear-gradient(135deg,#e9d7b5,#8a8f9c 45%,#23344f)"></div>
    <h3>Mid-Range</h3>
    <ul>
      <li><svg width="13" height="13" viewBox="0 0 13 13"><circle cx="6.5" cy="6.5" r="5.5" fill="none" stroke="#1f4fa6" stroke-width="1.5"/><path d="M4 6.5l2 2 3-4" fill="none" stroke="#1f4fa6" stroke-width="1.5"/></svg>Releases every 1.5 - 2 months</li>
      <li><svg width="13" height="13" viewBox="0 0 13 13"><circle cx="6.5" cy="6.5" r="5.5" fill="none" stroke="#1f4fa6" stroke-width="1.5"/><path d="M4 6.5l2 2 3-4" fill="none" stroke="#1f4fa6" stroke-width="1.5"/></svg>Full testing by my team prior to release</li>
      <li><svg width="13" height="13" viewBox="0 0 13 13"><circle cx="6.5" cy="6.5" r="5.5" fill="none" stroke="#1f4fa6" stroke-width="1.5"/><path d="M4 6.5l2 2 3-4" fill="none" stroke="#1f4fa6" stroke-width="1.5"/></svg>Priority support during normal business hours, always available for emergencies</li>
    </ul>
    <span class="learn">Learn More <svg width="14" height="14" viewBox="0 0 14 14"><circle cx="7" cy="7" r="6" fill="none" stroke="#1f4fa6" stroke-width="1.6"/><path d="M4 7h6M7.5 4.5L10 7 7.5 9.5" fill="none" stroke="#1f4fa6" stroke-width="1.6"/></svg></span>
  </article>
</section>

<div class="about-ring"></div>
<div class="about-img" role="img" aria-label="Developer at a desk studying trading charts on a monitor"></div>
<h2 class="about-title">About Us</h2>
<div class="about-copy">
  <p>Ledgerwise Forge provides a complete service that handles the development, IT operations and support for your cryptocurrency. Cryptocurrency development can be difficult and complex, and a quality development team is hard to find and expensive.</p>
  <p>Ledgerwise Forge has an experienced team that has helped several clients launch and enhance their cryptocurrencies, including successfully running the Nevira cryptocurrency since 2017, and writing a next-generation cryptocurrency from scratch.</p>
</div>
<a class="btn about-btn">Read More</a>

<h2 class="section-title" style="top:2802px">Client Testimonials</h2>
<div class="review" style="left:110px"><div class="avatar" role="img" aria-label="Client portrait"></div><h3>John Smith</h3><div class="stars">★★★★★</div><p>Lorem ipsum dolor sit amet, consectetur adip iscing elit, sed do eiusmod tempor incididu ntut labore et dolore magna aliquaudet enimad minim veniam quis.</p></div>
<div class="review" style="left:441px"><div class="avatar" role="img" aria-label="Client portrait"></div><h3>John Smith</h3><div class="stars">★★★★★</div><p>Lorem ipsum dolor sit amet, consectetur adip iscing elit, sed do eiusmod tempor incididu ntut labore et dolore magna aliquaudet enimad minim veniam quis.</p></div>
<div class="review" style="left:770px"><div class="avatar" role="img" aria-label="Client portrait"></div><h3>John Smith</h3><div class="stars">★★★★★</div><p>Lorem ipsum dolor sit amet, consectetur adip iscing elit, sed do eiusmod tempor incididu ntut labore et dolore magna aliquaudet enimad minim veniam quis.</p></div>

<section class="cta">
  <h2>Schedule a Free Consultation</h2>
  <p>Lorem ipsum dolor sit amet, consectetur adipiscing elit, sed do eiusmod tempor incididunt ut labore et dolore magna aliqua. Ut enim ad minim veniam, quis nostrud exercitation ullamco laboris nisi ut aliquip ex ea commodo consequat. Duis aute irure dolor in reprehenderit in voluptate velit esse cillum dolore eu fugiat nulla pariatur excepteur.</p>
  <a class="btn cta-btn">Get Started</a>
</section>
<svg class="cta-curve" width="1200" height="162" viewBox="0 0 1200 162"><path d="M0,150 Q600,-110 1200,150 L1200,162 L0,162 Z" fill="#f4f4f5"/></svg>

<footer class="site-footer">
  <div class="brand"><span class="brand-mark"></span><span class="brand-name">Ledgerwise<br>Forge</span></div>
  <div class="socials"><span></span><span></span><span></span><span></span></div>
  <div class="foot-col" style="left:384px"><h4>Quick Links</h4><ul>
    <li><svg width="13" height="13" viewBox="0 0 14 14"><circle cx="7" cy="7" r="6" fill="none" stroke="#1f4fa6" stroke-width="1.6"/><path d="M4 7h6M7.5 4.5L10 7 7.5 9.5" fill="none" stroke="#1f4fa6" stroke-width="1.6"/></svg>Home</li>
    <li><svg width="13" height="13" viewBox="0 0 14 14"><circle cx="7" cy="7" r="6" fill="none" stroke="#1f4fa6" stroke-width="1.6"/><path d="M4 7h6M7.5 4.5L10 7 7.5 9.5" fill="none" stroke="#1f4fa6" stroke-width="1.6"/></svg>About Us</li>
    <li><svg width="13" height="13" viewBox="0 0 14 14"><circle cx="7" cy="7" r="6" fill="none" stroke="#1f4fa6" stroke-width="1.6"/><path d="M4 7h6M7.5 4.5L10 7 7.5 9.5" fill="none" stroke="#1f4fa6" stroke-width="1.6"/></svg>Our Services</li>
    <li><svg width="13" height="13" viewBox="0 0 14 14"><circle cx="7" cy="7" r="6" fill="none" stroke="#1f4fa6" stroke-width="1.6"/><path d="M4 7h6M7.5 4.5L10 7 7.5 9.5" fill="none" stroke="#1f4fa6" stroke-width="1.6"/></svg>Our Methods</li>
    <li><svg width="13" height="13" viewBox="0 0 14 14"><circle cx="7" cy="7" r="6" fill="none" stroke="#1f4fa6" stroke-width="1.6"/><path d="M4 7h6M7.5 4.5L10 7 7.5 9.5" fill="none" stroke="#1f4fa6" stroke-width="1.6"/></svg>Contact Us</li>
  </ul></div>
  <div class="foot-col" style="left:552px"><h4>About Links</h4><ul>
    <li><svg width="13" height="13" viewBox="0 0 14 14"><circle cx="7" cy="7" r="6" fill="none" stroke="#1f4fa6" stroke-width="1.6"/><path d="M4 7h6M7.5 4.5L10 7 7.5 9.5" fill="none" stroke="#1f4fa6" stroke-width="1.6"/></svg>Blog</li>
    <li><svg width="13" height="13" viewBox="0 0 14 14"><circle cx="7" cy="7" r="6" fill="none" stroke="#1f4fa6" stroke-width="1.6"/><path d="M4 7h6M7.5 4.5L10 7 7.5 9.5" fill="none" stroke="#1f4fa6" stroke-width="1.6"/></svg>Search</li>
    <li><svg width="13" height="13" viewBox="0 0 14 14"><circle cx="7" cy="7" r="6" fill="none" stroke="#1f4fa6" stroke-width="1.6"/><path d="M4 7h6M7.5 4.5L10 7 7.5 9.5" fill="none" stroke="#1f4fa6" stroke-width="1.6"/></svg>Privacy Policy</li>
    <li><svg width="13" height="13" viewBox="0 0 14 14"><circle cx="7" cy="7" r="6" fill="none" stroke="#1f4fa6" stroke-width="1.6"/><path d="M4 7h6M7.5 4.5L10 7 7.5 9.5" fill="none" stroke="#1f4fa6" stroke-width="1.6"/></svg>Terms Of Conditions</li>
  </ul></div>
  <div class="foot-col" style="left:780px"><h4>Get Our Newsletter</h4></div>
  <div class="newsletter">Enter Email Address<b><svg width="18" height="18" viewBox="0 0 18 18"><path d="M2 9L16 2 12 16 9 10z" fill="#fff"/></svg></b></div>
  <div class="foot-rule"></div>
  <div class="copyright">Copyrights 2021 LEDGERWISE FORGE. All Rights Reserved</div>
</footer>

</body>
</html>
```